Tech business card design

We need an amazing business card design for our new business 'Pexla' a marketing tech startup based in Sydney, Australia. We provide an online marketplace for businesses to search and buy advertising media, connect with service providers and learn more about marketing. We wish to communicate 'cool tech', reliability and professionalism and design based around our logo.

Target Market(s)

Business Owners

Contact Information for Business Card

Name
Position
Email Address
Website
Phone Number

Font styles to use
Other font styles liked:
• Avenir & Avenir Next

Colors

Designer to choose colors to be used in the design.

```html
<!DOCTYPE html>
<html lang="en">
<head>
<meta charset="utf-8">
<title>Pexla Business Card</title>
<link href="https://fonts.googleapis.com/css2?family=Roboto:wght@400;500;700;900&display=swap" rel="stylesheet">
<style>
  :root {
    --stage: #1c1c1c;
    --navy: #120f3f;
    --navy-pattern: #1c1a52;
    --card-white: #f1f1f1;
    --ink: #16143d;
    --text-grey: #555555;
    --rule: #9a9a9a;
    --white: #ffffff;
  }
  * { margin: 0; padding: 0; box-sizing: border-box; }
  html, body {
    width: 1200px; height: 900px; overflow: hidden;
    background: var(--stage);
    font-family: "Roboto", Arial, sans-serif;
  }
  .card {
    position: absolute; left: 332px; width: 556px; height: 316px;
  }
  .card-back {
    top: 134px;
    background: var(--navy);
  }
  .card-back .pattern-fill {
    position: absolute; inset: 0;
    background: linear-gradient(135deg, var(--navy-pattern), var(--navy) 60%, var(--navy-pattern));
  }
  .card-back .corner-name {
    position: absolute; right: 60px; bottom: 52px;
    color: var(--white); font-weight: 700; font-size: 24px; letter-spacing: -0.5px;
  }
  .card-front {
    top: 488px;
    background: linear-gradient(135deg, #e9e9e9, var(--card-white) 55%, #f6f6f6);
  }
  .brand-name {
    position: absolute; left: 78px; top: 148px;
    font-size: 74px; font-weight: 900; color: var(--ink); letter-spacing: -1px; line-height: 1;
    transform: translateY(-50%);
  }
  .divider {
    position: absolute; left: 302px; top: 114px; width: 2px; height: 110px;
    background: var(--rule);
  }
  .contact-block { position: absolute; left: 322px; top: 110px; }
  .person-name { font-size: 24px; font-weight: 700; color: var(--ink); line-height: 1.1; }
  .person-role { font-size: 15px; color: var(--text-grey); margin-top: 2px; }
  .contact-list { list-style: none; margin-top: 18px; }
  .contact-list li {
    display: flex; align-items: center; gap: 8px;
    font-size: 13.5px; color: var(--text-grey); height: 19.5px;
  }
  .contact-list svg { width: 11px; height: 11px; fill: var(--ink); flex: none; }
</style>
</head>
<body>
  <section class="card card-back">
    <div class="pattern-fill" role="img" aria-label="Diagonal repeating pattern of the brand name in dark navy tones"></div>
    <span class="corner-name">Pexla</span>
  </section>

  <section class="card card-front">
    <span class="brand-name">Pexla</span>
    <div class="divider"></div>
    <div class="contact-block">
      <p class="person-name">Marlon Vesk</p>
      <p class="person-role">Managing Director</p>
      <ul class="contact-list">
        <li>
          <svg viewBox="0 0 24 24" aria-hidden="true"><path d="M6.6 10.8a15.1 15.1 0 0 0 6.6 6.6l2.2-2.2a1 1 0 0 1 1-.25 11.4 11.4 0 0 0 3.6.57 1 1 0 0 1 1 1V20a1 1 0 0 1-1 1A17 17 0 0 1 3 4a1 1 0 0 1 1-1h3.5a1 1 0 0 1 1 1c0 1.25.2 2.45.57 3.6a1 1 0 0 1-.25 1z"/></svg>
          123 456 7890
        </li>
        <li>
          <svg viewBox="0 0 24 24" aria-hidden="true"><path d="M2 5h20v2l-10 6L2 7z"/><path d="M2 9l10 6 10-6v10H2z"/></svg>
          info@yourwebsite.com
        </li>
        <li>
          <svg viewBox="0 0 24 24" aria-hidden="true"><path d="M12 2a10 10 0 1 0 0 20 10 10 0 0 0 0-20zm0 2c.9 1.2 1.7 2.9 2 5h-4c.3-2.1 1.1-3.8 2-5zM9.2 4.5C8.6 5.8 8.2 7.3 8 9H4.6a8 8 0 0 1 4.6-4.5zm5.6 0A8 8 0 0 1 19.4 9H16c-.2-1.7-.6-3.2-1.2-4.5zM4.2 11H8v2H4.2a8 8 0 0 1 0-2zm5.8 0h4v2h-4zm6 0h3.8a8 8 0 0 1 0 2H16zM4.6 15H8c.2 1.7.6 3.2 1.2 4.5A8 8 0 0 1 4.6 15zm5.4 0h4c-.3 2.1-1.1 3.8-2 5-.9-1.2-1.7-2.9-2-5zm6 0h3.4a8 8 0 0 1-4.6 4.5c.6-1.3 1-2.8 1.2-4.5z"/></svg>
          www.yourwebsite.com
        </li>
      </ul>
    </div>
  </section>
</body>
</html>
```